Need Business Card for our Real Estate Business with Sales Executive's Picture

PANTONE 484 C ( RED)

PANTONE 2766 C ( BLUE

Industry/Entity Type

Real Estate

Contact Information for Business Card

Name, Mobile, email, & picture of Person
Agency Phone, address, Web address

Requirements
Must have
• Our Logo Colours, Agent Picture,

```html
<!DOCTYPE html>
<html lang="en">
<head>
<meta charset="utf-8">
<title>Meridian Real Estate – Business Card</title>
<link href="https://fonts.googleapis.com/css2?family=Cinzel:wght@400;600&family=Source+Sans+3:wght@400&display=swap" rel="stylesheet">
<style>
  :root {
    --stage: #828282;
    --navy: #08123a;
    --wine: #650a10;
    --white: #ffffff;
    --ink: #0d1a3d;
    --portrait-top: #3c4a78;
    --portrait-bottom: #1d2f6e;
  }
  * { margin: 0; padding: 0; box-sizing: border-box; }
  html, body { width: 1200px; height: 900px; overflow: hidden; }
  body { background: var(--stage); position: relative; font-family: "Source Sans 3", sans-serif; }

  .card {
    position: absolute; top: 306px; width: 440px; height: 272px;
    border-radius: 11px; overflow: hidden;
    box-shadow: 2px 4px 6px rgba(0,0,0,.35);
  }
  .card--front { left: 149px; background: var(--wine); }
  .card--back { left: 608px; background: var(--white); }

  .front__band { position: absolute; left: 0; top: 0; width: 100%; height: 118px; background: var(--navy); }

  .brand { position: absolute; font-family: "Cinzel", serif; font-weight: 400; text-align: center; white-space: nowrap; }
  .brand__name { display: block; line-height: 1; }
  .brand__tag { display: block; letter-spacing: 1.5px; }

  .card--front .brand { left: 22px; top: 40px; width: 208px; color: var(--white); z-index: 2; }
  .card--front .brand__name { font-size: 35px; letter-spacing: 1px; }
  .card--front .brand__tag { font-size: 9px; margin-top: 6px; }

  .agent__name {
    position: absolute; left: 22px; top: 126px;
    font-family: "Cinzel", serif; font-weight: 600; font-size: 17px;
    color: var(--white); letter-spacing: .5px;
  }
  .contact { position: absolute; left: 23px; top: 155px; list-style: none; color: var(--white); font-size: 12.5px; line-height: 16px; }
  .contact li { display: flex; align-items: center; gap: 6px; }
  .contact svg { width: 9px; height: 9px; fill: var(--white); flex: none; }
  .address { position: absolute; left: 21px; top: 224px; color: var(--white); font-size: 12.5px; line-height: 16px; }

  .portrait {
    position: absolute; left: 232px; top: 30px; width: 208px; height: 242px;
    background: linear-gradient(180deg, var(--portrait-top), var(--portrait-bottom));
    border-radius: 70px 70px 0 0;
  }

  .card--back .brand { left: 0; top: 156px; width: 100%; color: var(--ink); }
  .card--back .brand__name { font-size: 36px; letter-spacing: 2px; }
  .card--back .brand__tag { font-size: 10px; margin-top: 6px; }
</style>
</head>
<body>
  <section class="card card--front">
    <div class="front__band"></div>
    <div class="portrait" role="img" aria-label="Portrait photo of the sales executive in a navy suit and striped tie"></div>
    <div class="brand">
      <span class="brand__name">MERIDIAN</span>
      <span class="brand__tag">REAL ESTATE</span>
    </div>
    <h1 class="agent__name">Daniel Hartley</h1>
    <ul class="contact">
      <li><svg viewBox="0 0 10 10"><path d="M2.5 0h5v10h-5z M3.5 1v7h3V1z" fill-rule="evenodd"/></svg>055-987 654 321</li>
      <li><svg viewBox="0 0 10 10"><path d="M0 3c2-3 8-3 10 0v1.5H7.5V3h-5v1.5H0zM1.5 5h7l1 5h-9z"/></svg>055-987 654 321</li>
      <li><svg viewBox="0 0 10 10"><path d="M0 2h10v1L5 6 0 3zM0 4l5 3 5-3v4H0z"/></svg>hello@meridianre.com</li>
      <li><svg viewBox="0 0 10 10"><circle cx="5" cy="5" r="5"/></svg>www.meridianre.com</li>
    </ul>
    <p class="address">12345, Address Goes Here<br>Country Name, 123456.</p>
  </section>

  <section class="card card--back">
    <div class="brand">
      <span class="brand__name">MERIDIAN</span>
      <span class="brand__tag">REAL ESTATE</span>
    </div>
  </section>
</body>
</html>
```